7 P's for Healthcare Companies - Textbook Graphic

Can you create a graphic for me for a medical textbook? The goal is to show 7 critical features of a healthcare startup and the audience is physicians with limited business backgrounds.

Please include a picture of young, male emergency physician in the middle of the graphic. Show them evaluating an idea. Can you surround the physician with bold writing for the seven components, and use brief descriptions and simple images or graphics to illustrate the point?

The image should be somewhat formal, but it's OK to be lighthearded.

The seven P's and brief descriptions include the following:
Product: what is their market solution?
(Intellectual) Property: do they have a patent or trademark?
Product Clearance: how will they get RLT approval and NVB clearance?
Payment: how will they make money?
Pilots: have they applied their product in a healthcare setting?
Physician and Patient feedback: Do doctors and patients like their product?
Publication: do they have evidence their product works?

More detail and information is available at this website: https://kovantrel.com/blog/uncategorized/healthcare-framework/

I will need to own this image

```html
<!DOCTYPE html>
<html lang="en">
<head>
<meta charset="utf-8">
<title>7 P's for Healthcare Companies</title>
<link rel="stylesheet" href="https://fonts.googleapis.com/css2?family=Montserrat:wght@500;800;900&display=swap">
<style>
  :root {
    --navy: #1e2c3e;
    --paper: #ffffff;
    --icon-line: #ffffff;
    --figure-light: #b3b7b1;
    --figure-dark: #858b86;
  }
  html, body {
    margin: 0;
    padding: 0;
    width: 1200px;
    height: 1200px;
    overflow: hidden;
    background: var(--paper);
  }
  .canvas {
    position: relative;
    width: 1200px;
    height: 1200px;
    background: var(--paper);
    font-family: "Montserrat", sans-serif;
    color: var(--navy);
  }
  .wheel {
    position: absolute;
    inset: 0;
    z-index: 0;
  }
  .ring { fill: none; stroke: var(--navy); stroke-width: 15; }
  .node { fill: var(--navy); }
  .icon {
    fill: none;
    stroke: var(--icon-line);
    stroke-width: 2.6;
    stroke-linecap: round;
    stroke-linejoin: round;
  }
  .icon .solid { fill: var(--icon-line); stroke: none; }

  .physician-figure {
    position: absolute;
    left: 531px;
    top: 419px;
    width: 226px;
    height: 364px;
    border-radius: 90px 90px 14px 14px;
    background: linear-gradient(180deg, #e9eae8 0%, var(--figure-light) 45%, var(--figure-dark) 100%);
    z-index: 1;
  }

  .framework-title {
    position: absolute;
    left: 474px;
    top: 500px;
    margin: 0;
    font-weight: 900;
    font-size: 126px;
    line-height: 1;
    letter-spacing: -7px;
    color: var(--navy);
    z-index: 2;
  }

  .label {
    position: absolute;
    margin: 0;
    font-weight: 800;
    text-transform: uppercase;
    line-height: 1;
    white-space: nowrap;
    color: var(--navy);
    z-index: 3;
  }
  .label .row {
    display: flex;
    align-items: flex-end;
  }
  .label .initial {
    font-size: 50px;
    font-weight: 500;
    line-height: 0.74;
    margin-right: -24px;
  }
  .label .rest {
    font-size: 15px;
    letter-spacing: 0;
    line-height: 1;
  }
  .label .stack { display: flex; flex-direction: column; }
  .label .qualifier {
    display: block;
    font-size: 6.5px;
    letter-spacing: 0.3px;
    margin: 0 0 3px 17px;
  }
  .label .second-line {
    display: block;
    font-size: 15px;
    margin-top: 3px;
  }

  .label-publication { left: 450px; top: 212px; }
  .label-product { left: 719px; top: 212px; }
  .label-property { left: 924px; top: 414px; }
  .label-clearance { left: 839px; top: 857px; }
  .label-clearance .second-line { margin-left: -8px; }
  .label-payment { left: 590px; top: 962px; }
  .label-pilots { left: 281px; top: 817px; }
  .label-feedback { left: 192px; top: 389px; }
  .label-feedback .second-line { margin-left: 61px; }
</style>
</head>
<body>
<main class="canvas">
  <svg class="wheel" width="1200" height="1200" viewBox="0 0 1200 1200" aria-hidden="true">
    <circle class="ring" cx="633" cy="599" r="280"/>

    <!-- Publication: megaphone -->
    <g transform="translate(511 349)">
      <circle class="node" r="76"/>
      <g class="icon">
        <path d="M-38 8 L-14 -12 L14 -34 L20 18 L-10 16 L-30 26 Z"/>
        <ellipse cx="17" cy="-8" rx="9" ry="27" transform="rotate(-8 17 -8)"/>
        <circle cx="14" cy="-8" r="6"/>
        <path d="M-12 16 L-2 36 Q2 42 8 38 Q12 34 8 28 L0 16"/>
        <path d="M30 -26 Q40 -10 34 8"/>
        <path d="M36 -34 Q52 -10 42 16"/>
      </g>
    </g>

    <!-- Product: idea in a box -->
    <g transform="translate(754 348)">
      <circle class="node" r="76"/>
      <g class="icon">
        <path d="M-38 0 L0 -14 L38 0 L0 14 Z"/>
        <path d="M-32 2 L-32 30 L0 46 L32 30 L32 2"/>
        <path d="M0 14 L0 46"/>
        <path d="M-38 0 L-44 10 L-6 24 L0 14"/>
        <path d="M38 0 L44 10 L6 24 L0 14"/>
        <path d="M-8 -12 Q-16 -20 -12 -30 Q-6 -40 0 -40 Q6 -40 12 -30 Q16 -20 8 -12 Z"/>
        <path d="M-6 -8 L6 -8 M-5 -4 L5 -4"/>
        <path d="M0 -50 L0 -58 M-18 -44 L-24 -50 M18 -44 L24 -50 M-26 -30 L-34 -32 M26 -30 L34 -32"/>
      </g>
    </g>

    <!-- Intellectual Property: certificate scroll -->
    <g transform="translate(907 538)">
      <circle class="node" r="76"/>
      <g class="icon">
        <path d="M-26 -44 L36 -44 Q44 -44 44 -34 L44 -28 L34 -28"/>
        <path d="M-26 -44 Q-34 -44 -34 -34 L-34 26"/>
        <path d="M34 -38 L34 40 Q34 48 26 48 L-44 48 Q-52 48 -52 40 L-52 30 L20 30 L20 40 Q20 48 26 48"/>
        <path d="M-24 -30 L24 -30 M-24 -22 L24 -22 M-24 -14 L8 -14"/>
        <circle cx="6" cy="0" r="9"/>
        <circle cx="6" cy="0" r="4"/>
        <path d="M0 8 L-4 22 L2 18 L6 22 M12 8 L16 22 L10 18 L6 22"/>
      </g>
    </g>

    <!-- Product Clearance: checklist clipboard -->
    <g transform="translate(853 774)">
      <circle class="node" r="76"/>
      <g class="icon">
        <rect x="-38" y="-42" width="76" height="94" rx="6"/>
        <rect x="-16" y="-50" width="32" height="12" rx="3"/>
        <circle cx="-18" cy="-12" r="8"/>
        <path d="M-22 -12 L-19 -8 L-13 -16"/>
        <circle cx="-18" cy="12" r="8"/>
        <path d="M-22 12 L-19 16 L-13 8"/>
        <path d="M-4 -16 L26 -16 M-4 -8 L26 -8 M-4 8 L26 8 M-4 16 L26 16 M-22 32 L26 32"/>
      </g>
    </g>

    <!-- Payment: banknote in hand -->
    <g transform="translate(633 880)">
      <circle class="node" r="76"/>
      <g class="icon">
        <rect x="-46" y="-42" width="92" height="52" rx="2"/>
        <rect x="-40" y="-36" width="80" height="40"/>
        <circle cx="0" cy="-16" r="15"/>
        <path d="M5 -24 Q0 -28 -5 -24 Q-8 -20 -2 -17 Q6 -14 4 -9 Q0 -5 -6 -9 M0 -30 L0 -27 M0 -6 L0 -2"/>
        <path d="M-48 26 Q-36 18 -22 22 L6 22 Q12 24 8 30 L-12 32 M8 28 L34 18 Q44 16 42 24 Q34 32 16 38 L-20 42 L-40 46"/>
      </g>
    </g>

    <!-- Pilots: stethoscope -->
    <g transform="translate(414 774)">
      <circle class="node" r="76"/>
      <g class="icon">
        <circle class="solid" cx="-2" cy="-42" r="4"/>
        <circle class="solid" cx="34" cy="-42" r="4"/>
        <path d="M-2 -42 Q-6 -42 -6 -36 L-6 -6 Q-6 14 14 14 Q32 14 32 -6 L32 -36 Q32 -42 36 -42"/>
        <path d="M14 14 L14 34 Q14 50 -4 52 Q-26 52 -30 34 Q-32 20 -38 14"/>
        <circle cx="-40" cy="-2" r="10"/>
        <circle cx="-40" cy="-2" r="4"/>
        <path d="M-40 8 Q-40 12 -38 14"/>
      </g>
    </g>

    <!-- Physician and Patient Feedback: speech bubbles -->
    <g transform="translate(361 538)">
      <circle class="node" r="76"/>
      <g class="icon">
        <path d="M-46 -32 Q-46 -40 -38 -40 L12 -40 Q20 -40 20 -32 L20 -2 Q20 6 12 6 L-24 6 L-38 18 L-38 6 Q-46 6 -46 -2 Z"/>
        <path d="M20 -14 L42 -14 Q50 -14 50 -6 L50 22 Q50 30 42 30 L38 30 L38 42 L24 30 L-16 30 Q-24 30 -24 22 L-24 6"/>
        <path class="solid" d="M-13 -4 L-24 -16 Q-30 -24 -22 -28 Q-16 -30 -13 -24 Q-10 -30 -4 -28 Q4 -24 -2 -16 Z"/>
      </g>
    </g>
  </svg>

  <div class="physician-figure" role="img" aria-label="Illustration of a young male emergency physician in shirt, tie and cardigan, gesturing with an open hand while evaluating an idea"></div>

  <h1 class="framework-title">7P</h1>

  <p class="label label-publication"><span class="row"><span class="initial">P</span><span class="rest">ublication</span></span></p>

  <p class="label label-product"><span class="row"><span class="initial">P</span><span class="rest">roduct</span></span></p>

  <p class="label label-property"><span class="row"><span class="initial">P</span><span class="stack"><span class="qualifier">(Intellectual)</span><span class="rest">roperty</span></span></span></p>

  <p class="label label-clearance"><span class="row"><span class="initial">P</span><span class="rest">roduct</span></span><span class="second-line">Clearance</span></p>

  <p class="label label-payment"><span class="row"><span class="initial">P</span><span class="rest">ayment</span></span></p>

  <p class="label label-pilots"><span class="row"><span class="initial">P</span><span class="rest">ilots</span></span></p>

  <p class="label label-feedback"><span class="row"><span class="initial">P</span><span class="rest">hysician and patient</span></span><span class="second-line">Feedback</span></p>
</main>
</body>
</html>
```